Trovanta Overview and Demo Presentation

Objective:
Create a bold, visually engaging PowerPoint deck to present Trovanta’s sales process and system demo to local movers, emphasizing ease of use, increased profitability, and operational efficiency.
Key Elements:
• Design: High-impact graphics with Trovanta branding, minimal text, and clean layouts.
• Content: Step-by-step sales process, key selling points, system demo walkthrough, and a compelling call-to-action.
• Live Demo: Showcase Trovanta’s platform, focusing on instant guaranteed pricing, streamlined booking, and support features.
Deliverables:
A dynamic presentation designed to educate and convert local movers into Trovanta partners, ensuring seamless flow and strong audience engagement.

Target Market(s)

Local Movers

Industry/Entity Type

Household Goods Moving

Font styles to use
Sans Serif

Colors
0054AA
0677BA
7BADD7
CADEEF
E8F1F8
FFC000
F8CF3A
FAE287
FDF2CF
FEFAEE

Requirements
Must have
• Project Brief: Trovanta Sales Process Presentation Objective: Create a bold, visually engaging PowerPoint deck to present Trovanta’s sales process and system demo to local movers, emphasizing ease of use, increased profitability, and operational efficiency. Key Elements: • Design: High-impact graphics with Trovanta branding, minimal text, and clean layouts. • Content: Step-by-step sales process, key selling points, system demo walkthrough, and a compelling call-to-action. • Live Demo: Showcase Trovanta’s platform, focusing on instant guaranteed pricing, streamlined booking, and support features. Deliverables: A dynamic presentation designed to educate and convert local movers into Trovanta partners, ensuring seamless flow and strong audience engagement.

```html
<!DOCTYPE html>
<html lang="en">
<head>
<meta charset="utf-8">
<title>Trovanta Partner Overview Deck</title>
<link rel="stylesheet" href="https://fonts.googleapis.com/css2?family=Montserrat:wght@500;600;700;800&family=Nunito+Sans:wght@400;600;700;800&display=swap">
<style>
:root{
  --board:#9c9c9c;
  --navy:#1c3a7e;
  --blue:#1456b8;
  --sky:#1ba1e2;
  --yellow:#f9c846;
  --orange:#f7931e;
  --ink:#1f2430;
  --muted:#4a5060;
  --paper:#fbfcfe;
  --line:#cadeef;
  --grey:#c9ccd2;
}
*{box-sizing:border-box;margin:0;padding:0}
html,body{width:1026px;height:1200px;overflow:hidden;background:var(--board)}
body{position:relative;font-family:"Nunito Sans",Arial,sans-serif;color:var(--ink)}
.slide{position:absolute;width:443px;height:249px;background:var(--paper);overflow:hidden;box-shadow:0 6px 14px rgba(0,0,0,.18)}
.abs{position:absolute}
.title{position:absolute;left:25px;top:8px;font-family:"Montserrat",Arial,sans-serif;font-weight:700;font-size:15.5px;color:var(--navy);line-height:1.15}
.title .hl{color:var(--orange)}
.band-edge{position:absolute;right:0;top:0;width:178px;height:37px;background:var(--line);clip-path:polygon(0 0,100% 0,100% 100%,20% 100%)}
.band{position:absolute;right:0;top:0;width:173px;height:35px;background:var(--navy);clip-path:polygon(0 0,100% 0,100% 100%,20% 100%)}
.brand{position:absolute;font-family:"Montserrat",Arial,sans-serif;font-weight:600;color:#fff;display:flex;align-items:center;gap:5px;white-space:nowrap}
.brand .mark{width:9px;height:9px;background:currentColor;display:inline-block}
.band .brand{right:25px;top:9px;font-size:14px}
.foot{position:absolute;right:26px;bottom:6px;display:flex;align-items:center;gap:6px;font-size:4.6px;font-weight:700;color:var(--navy)}
.foot .pg{width:10px;height:10px;background:var(--orange);transform:rotate(45deg);display:flex;align-items:center;justify-content:center}
.foot .pg span{transform:rotate(-45deg);color:#fff;font-size:4.5px}
.ico{position:absolute;border-radius:50%;transform:translate(-50%,-50%);display:flex;align-items:center;justify-content:center;box-shadow:0 2px 5px rgba(20,40,90,.28),0 0 0 2px #fff}
.ico svg{width:52%;height:52%;fill:none;stroke:#fff;stroke-width:2;stroke-linecap:round;stroke-linejoin:round}
.c-navy{background:var(--navy)}.c-blue{background:var(--blue)}.c-sky{background:var(--sky)}.c-yellow{background:var(--yellow)}.c-orange{background:var(--orange)}
.photo{position:absolute}

.cover{background:var(--navy);color:#fff}
.cover .brand{left:25px;top:15px;font-size:13px}
.cover h1{position:absolute;left:25px;top:62px;font-family:"Montserrat",Arial,sans-serif;font-weight:700;font-size:22.5px;line-height:26px}
.cover .sub{position:absolute;left:25px;top:146px;font-size:11.3px;font-weight:400}
.cover .date{position:absolute;left:25px;top:170px;width:67px;height:15px;background:var(--orange);border-radius:2px;font-size:5.2px;font-weight:700;display:flex;align-items:center;justify-content:center;gap:3px}
.cover .date i{width:4px;height:4px;border:1px solid #fff;border-radius:1px;display:inline-block}
.cover .site{position:absolute;left:25px;top:226px;font-size:7px;font-weight:700}

.about-text{position:absolute;left:246px;top:77px;width:175px;font-size:6.7px;line-height:10.6px;color:var(--ink)}
.about-text p+p{margin-top:5px}

.lead{position:absolute;left:0;right:0;text-align:center;font-size:6.8px;line-height:10.5px;color:var(--ink)}
.card{position:absolute;top:83px;width:124px;height:136px;background:#fff;border:1.3px solid;border-radius:5px;padding:28px 11px 0;box-shadow:0 3px 7px rgba(20,40,90,.15)}
.card h3{font-family:"Montserrat",Arial,sans-serif;font-size:7.8px;font-weight:700;color:var(--navy)}
.card .tag{margin-top:3px;font-size:5.8px;line-height:9px;font-weight:600;color:var(--orange)}
.card p{margin-top:4px;font-size:5.8px;line-height:9.3px;color:var(--muted)}

.prob{position:absolute;width:190px}
.prob h4{font-size:6.5px;font-weight:800;color:var(--ink);display:flex;align-items:center;gap:6px}
.prob h4 i{width:4.5px;height:4.5px;background:var(--orange);transform:rotate(45deg)}
.prob p{margin:3px 0 0 10.5px;font-size:5.6px;line-height:8.6px;color:var(--muted)}

.feat{position:absolute;width:80px}
.feat h4{font-size:5px;font-weight:800;color:var(--ink);margin-bottom:2px}
.feat p{font-size:3.6px;line-height:5.9px;color:var(--muted)}
.feat.r{text-align:right}.feat.c{text-align:center}

.why{position:absolute;width:170px}
.why h4{font-size:7.3px;font-weight:800;color:var(--ink)}
.why p{margin-top:3px;font-size:5.6px;line-height:8.5px;color:var(--muted)}

.stat{position:absolute;width:80px;height:80px;border-radius:50%;transform:translate(-50%,-50%);color:#fff;display:flex;flex-direction:column;align-items:center;justify-content:center;text-align:center;box-shadow:0 4px 8px rgba(20,40,90,.3),0 0 0 2.5px #fff}
.stat b{font-family:"Montserrat",Arial,sans-serif;font-size:16px;font-weight:800;line-height:1}
.stat span{margin-top:4px;font-size:6px;line-height:9px;font-weight:600}
.lbl{position:absolute;font-size:8.5px;font-weight:600;color:var(--ink);transform:translateX(-50%)}
.proven{position:absolute;left:50%;top:220px;transform:translateX(-50%);font-family:"Montserrat",Arial,sans-serif;font-size:9px;font-weight:700;color:var(--orange)}

.step{position:absolute;width:96px;transform:translateX(-50%);text-align:center}
.step h4{font-size:5.2px;font-weight:800;color:var(--navy)}
.step p{margin-top:2px;font-size:3.9px;line-height:6.3px;color:var(--muted)}
.step p em{font-style:normal;color:var(--orange)}
</style>
</head>
<body>

<svg width="0" height="0" style="position:absolute" aria-hidden="true">
  <defs>
    <symbol id="i-phone" viewBox="0 0 24 24"><path d="M5 3h4l2 5-3 2a11 11 0 0 0 6 6l2-3 5 2v4a2 2 0 0 1-2 2A17 17 0 0 1 3 5a2 2 0 0 1 2-2z"/></symbol>
    <symbol id="i-pin" viewBox="0 0 24 24"><path d="M12 21s-6-6-6-11a6 6 0 0 1 12 0c0 5-6 11-6 11z"/><circle cx="12" cy="10" r="2.2"/></symbol>
    <symbol id="i-gear" viewBox="0 0 24 24"><circle cx="12" cy="12" r="3.5"/><circle cx="12" cy="12" r="8" stroke-dasharray="3 2.3" stroke-width="3"/></symbol>
    <symbol id="i-dollar" viewBox="0 0 24 24"><circle cx="12" cy="12" r="9"/><path d="M15 9c-1-1.5-6-1.5-6 .8s6 1.4 6 4c0 2.3-5 2.3-6 .7M12 6v12"/></symbol>
    <symbol id="i-check" viewBox="0 0 24 24"><rect x="5" y="4" width="14" height="16" rx="2"/><path d="M9 12l2 2 4-4"/></symbol>
    <symbol id="i-bulb" viewBox="0 0 24 24"><path d="M9 17h6M10 20h4M12 3a6 6 0 0 0-3 11v3h6v-3a6 6 0 0 0-3-11z"/></symbol>
    <symbol id="i-people" viewBox="0 0 24 24"><circle cx="8" cy="8" r="3"/><circle cx="16" cy="8" r="3"/><path d="M2 20c0-4 3-6 6-6s6 2 6 6M12 14c1-.6 2.4-1 4-1 3 0 6 2 6 6"/></symbol>
    <symbol id="i-doc" viewBox="0 0 24 24"><path d="M6 3h9l4 4v14H6z"/><path d="M9 11h7M9 15h5"/></symbol>
    <symbol id="i-cal" viewBox="0 0 24 24"><rect x="4" y="5" width="16" height="15" rx="2"/><path d="M4 10h16M8 3v4M16 3v4"/></symbol>
    <symbol id="i-eye" viewBox="0 0 24 24"><path d="M2 12s4-7 10-7 10 7 10 7-4 7-10 7S2 12 2 12z"/><circle cx="12" cy="12" r="3"/></symbol>
    <symbol id="i-arrow" viewBox="0 0 24 24"><path d="M5 19L19 5M10 5h9v9"/></symbol>
    <symbol id="i-target" viewBox="0 0 24 24"><circle cx="12" cy="12" r="9"/><circle cx="12" cy="12" r="5"/><circle cx="12" cy="12" r="1.5"/></symbol>
    <symbol id="i-tree" viewBox="0 0 24 24"><rect x="9" y="3" width="6" height="5"/><rect x="3" y="16" width="5" height="5"/><rect x="16" y="16" width="5" height="5"/><path d="M12 8v4M5.5 16v-4h13v4"/></symbol>
  </defs>
</svg>

<section class="slide cover" style="left:51px;top:54px">
  <div class="brand"><i class="mark"></i>Trovanta</div>
  <h1>Moving<br>For The Next<br>Generation</h1>
  <div class="sub">Partner Overview Presentation</div>
  <div class="date"><i></i>February 1, 2024</div>
  <div class="site">Trovanta.com</div>
  <div class="photo" role="img" aria-label="Photo of movers in blue overalls carrying boxes beside a van" style="left:235px;top:38px;width:160px;height:174px;background:linear-gradient(135deg,#d9dde3 0%,#8e9bb0 45%,#1f4fa8 70%,#b08a62 100%)"></div>
</section>

<section class="slide" style="left:531px;top:54px">
  <div class="title">Trovanta <span class="hl">Solution</span></div>
  <div class="band-edge"></div><div class="band"><div class="brand"><i class="mark"></i>Trovanta</div></div>
  <svg class="abs" style="left:0;top:0" width="443" height="249" viewBox="0 0 443 249" aria-hidden="true">
    <circle cx="222" cy="272" r="111" fill="none" stroke="#5a6275" stroke-width=".6" stroke-dasharray="2 2"/>
    <path d="M141 249 A81 70 0 0 1 303 249 Z" fill="#fff"/>
    <g stroke="#fff" stroke-width="1.5">
      <circle cx="120" cy="234" r="4" fill="var(--navy)"/>
      <circle cx="159" cy="181" r="4" fill="var(--blue)"/>
      <circle cx="222" cy="160" r="4" fill="var(--sky)"/>
      <circle cx="285" cy="181" r="4" fill="var(--yellow)"/>
      <circle cx="324" cy="234" r="4" fill="var(--orange)"/>
    </g>
  </svg>
  <div class="brand" style="left:50%;top:215px;transform:translateX(-50%);color:var(--blue);font-size:16px"><i class="mark"></i>Trovanta</div>
  <div class="ico c-navy" style="left:79px;top:204px;width:40px;height:40px"><svg><use href="#i-gear"/></svg></div>
  <div class="ico c-blue" style="left:133px;top:138px;width:40px;height:40px"><svg><use href="#i-phone"/></svg></div>
  <div class="ico c-sky" style="left:222px;top:111px;width:40px;height:40px"><svg><use href="#i-check"/></svg></div>
  <div class="ico c-yellow" style="left:312px;top:138px;width:40px;height:40px"><svg><use href="#i-pin"/></svg></div>
  <div class="ico c-orange" style="left:365px;top:204px;width:40px;height:40px"><svg><use href="#i-dollar"/></svg></div>
  <div class="feat c" style="left:182px;top:58px"><h4>BOOK NOW PAY LATER</h4><p>Moving has a high price tag, but no one has ever offered a pay later solution. Much less a no credit check offer.</p></div>
  <div class="feat r" style="left:76px;top:80px"><h4>ONE POINT OF CONTACT</h4><p>Today moves are sold from broker to broker until it's finally sold to a mover. Many entities involved means a confusing line of correspondence for the customer.</p></div>
  <div class="feat" style="left:289px;top:80px"><h4>GPS TRACKING</h4><p>Shoplyn has conditioned consumers to expect real-time tracking of goods. Only Trovanta enables you to track all of your belongings door to door.</p></div>
  <div class="feat r" style="left:22px;top:145px"><h4>ON-DEMAND PROCESS</h4><p>Trovanta automatically audits: Compliance, Insurance, Regulatory, Bonding, Background checks, and Quality.</p></div>
  <div class="feat" style="left:343px;top:145px"><h4>SIMPLE HONEST PRICING</h4><p>Trovanta's proprietary algorithms and data are backed up by checks and balances process giving the first instant pricing solution that won't change.</p></div>
  <div class="foot">Trovanta.com<span class="pg"><span>5</span></span></div>
</section>

<section class="slide" style="left:51px;top:335px">
  <div class="title">About <span class="hl">Us</span></div>
  <div class="band-edge"></div><div class="band"><div class="brand"><i class="mark"></i>Trovanta</div></div>
  <div class="photo" role="img" aria-label="Photo of a couple working on laptops at a table surrounded by moving boxes" style="left:25px;top:62px;width:197px;height:154px;background:linear-gradient(120deg,#e9edf2 0%,#c7cfd8 40%,#8b7a66 75%,#4b5568 100%)"></div>
  <div class="about-text">
    <p>Trovanta is the next logical evolution in professional moving. Professional moving clients have battled soaring prices, acute capacity problems and deteriorating service levels.</p>
    <p>Trovanta was founded by lifelong moving professionals who have developed the answer to better moving services. Poised as THE industry disruptor, we deliver faster, offer guaranteed prices and even offer no credit check financing options. We are a technology first organization using proprietary software to deliver moving's best service experience.</p>
  </div>
  <div class="foot">Trovanta.com<span class="pg"><span>2</span></span></div>
</section>

<section class="slide" style="left:531px;top:335px">
  <div class="title">Why Does <span class="hl">Trovanta Matter?</span></div>
  <div class="band-edge"></div><div class="band"><div class="brand"><i class="mark"></i>Trovanta</div></div>
  <div class="lead" style="top:47px">Partner with Trovanta and elevate your moving business by expanding your reach and<br>capabilities without the hassle.</div>
  <svg class="abs" style="left:0;top:0" width="443" height="249" viewBox="0 0 443 249" aria-hidden="true">
    <circle cx="115" cy="156" r="79" fill="var(--orange)"/>
    <path d="M203 76 C240 110 240 200 203 236" fill="none" stroke="#3a4152" stroke-width=".7" stroke-dasharray="1.2 1.6"/>
    <circle cx="203" cy="76" r="1.6" fill="#3a4152"/><circle cx="203" cy="236" r="1.6" fill="#3a4152"/>
  </svg>
  <div class="photo" role="img" aria-label="Photo of a happy woman stretching on a sofa among moving boxes" style="left:47px;top:88px;width:136px;height:136px;border-radius:50%;background:linear-gradient(160deg,#c9d6dc 0%,#9aa9b2 45%,#f2c230 62%,#2f58a8 100%)"></div>
  <div class="ico c-navy" style="left:223px;top:107px;width:32px;height:32px"><svg><use href="#i-bulb"/></svg></div>
  <div class="ico c-blue" style="left:236px;top:156px;width:32px;height:32px"><svg><use href="#i-dollar"/></svg></div>
  <div class="ico c-sky" style="left:224px;top:206px;width:32px;height:32px"><svg><use href="#i-people"/></svg></div>
  <div class="why" style="left:251px;top:93px"><h4>MAXIMIZE OPPORTUNITIES</h4><p>Never miss out on another long distance move opportunity again.</p></div>
  <div class="why" style="left:264px;top:141px"><h4>EFFICIENT PRICING</h4><p>Easily quote competitive pricing and maintain desired profit margins.</p></div>
  <div class="why" style="left:251px;top:193px"><h4>HASSLE-FREE MANAGEMENT</h4><p>Schedule, pay and track moves all through Trovanta</p></div>
  <div class="foot">Trovanta.com<span class="pg"><span>6</span></span></div>
</section>

<section class="slide" style="left:51px;top:616px">
  <div class="title">Our <span class="hl">Vision</span></div>
  <div class="band-edge"></div><div class="band"><div class="brand"><i class="mark"></i>Trovanta</div></div>
  <div class="lead" style="top:47px">The traditional moving industry is broken, outdated, inefficient, and unable to change.</div>
  <div class="card" style="left:25px;border-color:var(--navy)"><h3>OUR VISION</h3><div class="tag">Revolutionize the moving industry by providing great value to everyone involved</div><p>Trovanta Customers - Consumers, Movers, Corporate Clients, and Relocation Management Companies all receive better value with Trovanta than anywhere else.</p></div>
  <div class="card" style="left:159px;border-color:var(--sky)"><h3>OUR MISSION</h3><div class="tag">Disrupt a $86B sleepy giant of an inefficient industry</div><p>Trovanta's deep understanding of the professional moving industry, supported by extensive market research has set Trovanta up for ultimate success in disrupting this industry by creating cost-saving efficiencies throughout.</p></div>
  <div class="card" style="left:294px;border-color:var(--yellow)"><h3>OUR GOAL</h3><div class="tag">Becoming the moving platform of choice</div><p>As Trovanta's market share grows, the customer acquisition cost and operational cost plummets. This creates even more market penetration, more efficiencies, and exponential growth.</p></div>
  <div class="ico c-navy" style="left:54px;top:82px;width:33px;height:33px"><svg><use href="#i-eye"/></svg></div>
  <div class="ico c-sky" style="left:188px;top:82px;width:33px;height:33px"><svg><use href="#i-arrow"/></svg></div>
  <div class="ico c-yellow" style="left:322px;top:82px;width:33px;height:33px"><svg><use href="#i-target"/></svg></div>
  <div class="foot">Trovanta.com<span class="pg"><span>3</span></span></div>
</section>

<section class="slide" style="left:531px;top:616px">
  <div class="title">Revolutionizing<br><span class="hl">The Moving Industry With AI</span></div>
  <div class="band-edge"></div><div class="band"><div class="brand"><i class="mark"></i>Trovanta</div></div>
  <div class="lead" style="top:55px;left:45px;right:45px">Trovanta is transforming the $90-100B moving industry by leveraging AI, GPS, and automated compliance to deliver the first instant guaranteed pricing platform. We're cutting out inefficiencies and middlemen to improve costs and service quality.</div>
  <div class="lbl" style="left:134px;top:99px">TO BUILD</div>
  <div class="lbl" style="left:340px;top:99px">TO PROVE</div>
  <div class="stat c-navy" style="left:68px;top:143px"><b>$1.9M</b><span>Revenue<br>Successfully Raised</span></div>
  <div class="stat c-blue" style="left:171px;top:167px"><b>$5</b><span>Appraised Tech<br>Stack</span></div>
  <div class="stat c-sky" style="left:273px;top:143px"><b>$500K</b><span>Additional Raise</span></div>
  <div class="stat c-yellow" style="left:376px;top:167px"><b>B21</b><span>Successful Model</span></div>
  <div class="proven">PROVEN MODEL</div>
  <div class="foot">Trovanta.com<span class="pg"><span>7</span></span></div>
</section>

<section class="slide" style="left:51px;top:897px">
  <div class="title">Moving’s <span class="hl">Problems</span></div>
  <div class="band-edge"></div><div class="band"><div class="brand"><i class="mark"></i>Trovanta</div></div>
  <svg class="abs" style="left:0;top:0" width="443" height="249" viewBox="0 0 443 249" aria-hidden="true">
    <circle cx="109" cy="143" r="75" fill="none" stroke="#3a4152" stroke-width=".7" stroke-dasharray="2.5 2"/>
    <circle cx="109" cy="143" r="61" fill="#fff" style="filter:drop-shadow(0 2px 6px rgba(27,80,180,.25))"/>
    <g stroke-width="1.2" fill="#fff">
      <circle cx="162" cy="90" r="2.5" stroke="var(--navy)"/>
      <circle cx="180" cy="119" r="2.5" stroke="var(--blue)"/>
      <circle cx="183" cy="146" r="2.5" stroke="var(--sky)"/>
      <circle cx="167" cy="190" r="2.5" stroke="var(--yellow)"/>
    </g>
  </svg>
  <div class="brand" style="left:109px;top:131px;transform:translateX(-50%);color:var(--blue);font-size:17px"><i class="mark"></i>Trovanta</div>
  <div class="ico c-navy" style="left:186px;top:74px;width:30px;height:30px"><svg><use href="#i-dollar"/></svg></div>
  <div class="ico c-blue" style="left:207px;top:115px;width:30px;height:30px"><svg><use href="#i-gear"/></svg></div>
  <div class="ico c-sky" style="left:207px;top:159px;width:30px;height:30px"><svg><use href="#i-people"/></svg></div>
  <div class="ico c-yellow" style="left:189px;top:206px;width:30px;height:30px"><svg><use href="#i-doc"/></svg></div>
  <div class="prob" style="left:211px;top:59px"><h4><i></i>COST</h4><p>Moving cost has skyrocketed over the last three years. Charges have increased 38% since 2018.</p></div>
  <div class="prob" style="left:232px;top:111px"><h4><i></i>CAPACITY</h4><p>Long-haul driver shortages and limited equipment coupled with growing demand has pushed capacity to a crisis state</p></div>
  <div class="prob" style="left:232px;top:150px"><h4><i></i>SERVICES</h4><p>Quality labor has been difficult to source and afford. Virtually all RMC's report a decline in service quality</p></div>
  <div class="prob" style="left:211px;top:191px"><h4><i></i>TRANSPARENCY</h4><p>Too many margin layers...van line, agent, driver and help. In addition, charges are convoluted and confusing</p></div>
  <div class="foot">Trovanta.com<span class="pg"><span>4</span></span></div>
</section>

<section class="slide" style="left:531px;top:897px">
  <div class="title">How <span class="hl">It Works</span></div>
  <div class="band-edge"></div><div class="band"><div class="brand"><i class="mark"></i>Trovanta</div></div>
  <div class="lead" style="top:49px">Trovanta is a tech-driven moving company that automates the move management process.</div>
  <div class="lead" style="top:66px;left:45px;right:45px">Our proprietary technology streamlines the process, offering customers and partners a seamless experience and peace of mind. We have simplified the complex and often stressful task of moving.</div>
  <svg class="abs" style="left:0;top:0" width="443" height="249" viewBox="0 0 443 249" aria-hidden="true">
    <line x1="31" y1="153" x2="413" y2="153" stroke="var(--grey)" stroke-width="1"/>
    <circle cx="31" cy="153" r="3.5" fill="#fff" stroke="var(--grey)" stroke-width="1.5"/>
    <circle cx="413" cy="153" r="3.5" fill="#fff" stroke="var(--grey)" stroke-width="1.5"/>
  </svg>
  <div class="ico c-navy" style="left:71px;top:153px;width:29px;height:29px"><svg><use href="#i-bulb"/></svg></div>
  <div class="ico c-blue" style="left:131px;top:153px;width:29px;height:29px"><svg><use href="#i-doc"/></svg></div>
  <div class="ico c-sky" style="left:191px;top:153px;width:29px;height:29px"><svg><use href="#i-dollar"/></svg></div>
  <div class="ico c-yellow" style="left:251px;top:153px;width:29px;height:29px"><svg><use href="#i-cal"/></svg></div>
  <div class="ico c-orange" style="left:312px;top:153px;width:29px;height:29px"><svg><use href="#i-people"/></svg></div>
  <div class="ico c-orange" style="left:372px;top:153px;width:29px;height:29px"><svg><use href="#i-tree"/></svg></div>
  <div class="step" style="left:71px;top:109px"><h4>SPOT AN OPPORTUNITY</h4><p>Do not let a long-distance move prospect slip away.</p></div>
  <div class="step" style="left:191px;top:109px"><h4>SET YOUR PRICE</h4><p>Offer a suitable price to your customer and secure a deal.</p></div>
  <div class="step" style="left:312px;top:109px"><h4>STAY INFORMED</h4><p>We ensure constant communication so you can update your customers at every step.</p></div>
  <div class="step" style="left:131px;top:180px"><h4>GET A QUOTE</h4><p>Quickly input details on <em>Trovanta.com.</em></p></div>
  <div class="step" style="left:251px;top:180px"><h4>SEAMLESS SCHEDULING</h4><p>Use <em>Trovanta.com</em> to schedule the service. Just pay the deposit and leave the rest to us. You can even take advantage of our move concierge if that is easier.</p></div>
  <div class="step" style="left:372px;top:180px"><h4>FLEXIBLE PRICING STRUCTURE</h4><p>You decide the charges. We only bill you, letting you keep your desired profit.</p></div>
  <div class="foot">Trovanta.com<span class="pg"><span>8</span></span></div>
</section>

</body>
</html>
```